Larkspur Energy - Stock Certificate

We need a custom designed stock certificate that represents the look of our company logo but also have a cool look compared to a standard stock certificate. We thinking we want the logo in gold. Our website is https://www.larkspurenergyusa.example.

We are wanting the certificate to look very professional and really cool, we have sales agents that work for the company and we are creating a program by which the sales agents can gain ownership in the company. So the certificates need to have a very cool appeal and that provides a sense of pride in owning "Units" in Larkspur Energy.

Reason: Extending so other board members can vote as well, thank you all!

Target Market(s)

Stock/Shareholders

Industry/Entity Type

It Company

Font styles to use
Script

Requirements
Must have
• Must look like a stock certificate, must use our logo which the psd file for it was attached.
Nice to have
• Nice to have the logo in gold

```html
<!DOCTYPE html>
<html lang="en">
<head>
<meta charset="utf-8">
<title>Larkspur Energy – Stock Certificate</title>
<link rel="stylesheet" href="https://fonts.googleapis.com/css2?family=UnifrakturCook:wght@700&family=Great+Vibes&family=Arimo:wght@400&family=Open+Sans:ital@1&family=Montserrat:wght@500&display=swap">
<style>
  :root {
    --paper: #ffffff;
    --backdrop: #ececec;
    --ink: #1b1b1b;
    --script-ink: #111111;
    --fill-ink: #6a4a1c;
    --title-dark: #b8410c;
    --title-light: #e0801e;
    --frame-orange: #d2520e;
    --frame-yellow: #ffd51f;
    --gold: #e39a25;
    --gold-deep: #b8560e;
  }
  * { margin: 0; padding: 0; box-sizing: border-box; }
  html, body { width: 1200px; height: 848px; overflow: hidden; background: var(--paper); }
  .certificate { position: relative; width: 1200px; height: 848px; background: var(--paper); color: var(--ink); font-family: "Arimo", Arial, sans-serif; }
  .backdrop { position: absolute; left: 24px; top: 20px; width: 1152px; height: 806px;
    background: radial-gradient(ellipse at 55% 40%, var(--backdrop) 0%, #f3f3f3 55%, #fafafa 100%); }
  .frame { position: absolute; left: 0; top: 0; }
  .title { position: absolute; left: 380px; width: 744px; top: 118px; text-align: center;
    font-family: "UnifrakturCook", serif; font-weight: 700; font-size: 88px; line-height: 1;
    background: linear-gradient(180deg, var(--title-light), var(--title-dark) 60%);
    -webkit-background-clip: text; background-clip: text; color: transparent; }
  .line-text { position: absolute; left: 360px; width: 784px; text-align: center; font-size: 19px; line-height: 1; }
  .certifies { top: 253px; }
  .holder { position: absolute; left: 516px; top: 300px; width: 476px; height: 100px; border-bottom: 1.5px solid var(--ink); text-align: center;
    font-family: "Great Vibes", cursive; font-size: 88px; line-height: 1.2; color: var(--script-ink); }
  .row { display: flex; justify-content: center; align-items: flex-end; white-space: pre; }
  .entitled { top: 424px; }
  .class-row { top: 456px; }
  .blank { display: inline-block; border-bottom: 1.5px solid var(--ink); text-align: center;
    font-family: "Great Vibes", cursive; color: var(--fill-ink); font-size: 28px; line-height: 1; height: 27px; }
  .blank-shares { width: 50px; }
  .blank-par { width: 168px; }
  .blank-class { width: 236px; font-size: 22px; color: var(--ink); margin-right: 14px; }
  .terms-1 { top: 509px; }
  .terms-2 { top: 535px; }
  .witness { top: 587px; }
  .signature { position: absolute; top: 650px; width: 142px; }
  .signature-mark { height: 62px; border-bottom: 1.5px solid var(--ink);
    background: linear-gradient(180deg, transparent 30%, rgba(0,0,0,0.05) 60%, transparent 95%); }
  .signature-label { font-family: "Open Sans", sans-serif; font-style: italic; font-size: 21px; padding-left: 28px; margin-top: 2px; }
  .sign-left { left: 534px; }
  .sign-right { left: 812px; }
  .brand { position: absolute; left: 64px; top: 212px; width: 296px; }
  .brand-mark { width: 230px; height: 230px; margin: 40px auto 0; border-radius: 50%;
    background: radial-gradient(circle at 50% 50%, #ffe9a8 0%, var(--gold) 35%, var(--gold-deep) 100%); }
  .brand-name { margin-top: 74px; text-align: center; font-family: "Montserrat", sans-serif; font-weight: 500; font-size: 30px; color: var(--ink); letter-spacing: 1px; }
</style>
</head>
<body>
<main class="certificate">
  <div class="backdrop" role="img" aria-label="Faint world map backdrop"></div>

  <svg class="frame" width="1200" height="848" viewBox="0 0 1200 848" aria-hidden="true">
    <defs>
      <linearGradient id="frameGradient" x1="0" y1="0" x2="1" y2="1">
        <stop offset="0" stop-color="var(--frame-orange)"/>
        <stop offset="0.55" stop-color="#f08a1a"/>
        <stop offset="0.8" stop-color="var(--frame-yellow)"/>
        <stop offset="1" stop-color="#f07a14"/>
      </linearGradient>
    </defs>
    <path d="M70,16 H1130 A52,52 0 0 0 1182,68 V780 A52,52 0 0 0 1130,832 H70 A52,52 0 0 0 18,780 V68 A52,52 0 0 0 70,16 Z"
          fill="none" stroke="url(#frameGradient)" stroke-width="6"/>
  </svg>

  <section class="brand">
    <div class="brand-mark"></div>
    <p class="brand-name">Larkspur Energy</p>
  </section>

  <h1 class="title">Stock Certificate</h1>

  <p class="line-text certifies">This certifies that</p>
  <p class="holder">John Doe</p>

  <p class="line-text row entitled">is entitled to <span class="blank blank-shares">55</span> shares of the par value of <span class="blank blank-par">120$</span>each of the</p>
  <p class="line-text row class-row"><span class="blank blank-class">Common stock</span>of  the  Larkspur Energy Company</p>

  <p class="line-text terms-1">transferable in person or by Attorney only in the books of the Company and upon</p>
  <p class="line-text terms-2">the surrender of this Certificate.</p>

  <p class="line-text witness">In witness whereof the Larkspur Energy Company  has caused this Certificate to be</p>

  <div class="signature sign-left">
    <div class="signature-mark" role="img" aria-label="Handwritten signature"></div>
    <p class="signature-label">Signature</p>
  </div>
  <div class="signature sign-right">
    <div class="signature-mark" role="img" aria-label="Handwritten signature"></div>
    <p class="signature-label">Signature</p>
  </div>
</main>
</body>
</html>
```